Business Cards used to invite people to our church

We are a church and have need of a business card sized advertisement that allows our members to hand them out in order to invite people to the church. I need the front of the card to say "You're Invited" or "Come Check us out". with the service times on the back of the card later.
I have attached one of the OLD cards we have used in the past, but we want a complete makeover, into a more modern style that does not require the image.
I am also replacing the old logo with a newer "flat" logo which is attached.
Please use marketing colors. (blue or red or something that catches attention)
Create a card that DOES NOT have the picture of the two people on the front
The information on the sample card back is correct to go onto new card
Target Market(s)
anyone
Industry/Entity Type
Business
Contact Information for Business Card
sertice times and address information which you can get from the sample card I uploaded. It should have "You're Invited" or "Come Check us out" on the front of the card with out logo.

```html
<!DOCTYPE html>
<html lang="en">
<head>
<meta charset="utf-8">
<title>Invitation Card – Front and Back</title>
<link rel="stylesheet" href="https://fonts.googleapis.com/css2?family=Quicksand:wght@500&family=Open+Sans:wght@400;600;700&display=swap">
<style>
  :root {
    --backdrop: #3a332f;
    --card: #0c0c0c;
    --ink: #ffffff;
    --ink-soft: #d9d9d9;
    --silver: #b8b8b8;
  }
  * { box-sizing: border-box; margin: 0; padding: 0; }
  html, body { width: 1200px; height: 900px; overflow: hidden; }
  body {
    background: var(--backdrop);
    display: flex;
    align-items: center;
    justify-content: center;
    gap: 60px;
    font-family: "Open Sans", Arial, sans-serif;
  }
  .card {
    width: 500px;
    height: 290px;
    background: var(--card);
    border-radius: 4px;
    box-shadow: 0 10px 30px rgba(0,0,0,.45);
    color: var(--ink);
    position: relative;
  }
  /* Front */
  .card-front {
    display: flex;
    align-items: center;
    justify-content: center;
  }
  .invite-headline {
    font-family: "Quicksand", "Open Sans", sans-serif;
    font-weight: 500;
    text-align: center;
    line-height: 1.05;
  }
  .invite-headline .word-large { display: block; font-size: 64px; }
  .invite-headline .word-small { display: block; font-size: 40px; }

  /* Back */
  .card-back {
    padding: 26px 40px 0;
    text-align: center;
  }
  .brand {
    display: flex;
    align-items: center;
    justify-content: center;
    gap: 10px;
    margin-bottom: 16px;
  }
  .brand-mark {
    width: 18px;
    height: 18px;
    background: var(--silver);
  }
  .brand-name {
    font-weight: 600;
    font-size: 20px;
    letter-spacing: 1.5px;
    color: var(--silver);
  }
  .contact {
    font-weight: 700;
    font-size: 14px;
    line-height: 1.45;
    margin-bottom: 16px;
  }
  .schedule {
    list-style: none;
    width: 320px;
    margin: 0 auto;
    font-size: 13px;
    color: var(--ink-soft);
  }
  .schedule li {
    display: flex;
    align-items: baseline;
    line-height: 1.9;
  }
  .schedule .leader {
    flex: 1;
    border-bottom: 1.5px dotted var(--ink-soft);
    margin: 0 4px;
    transform: translateY(-3px);
  }
</style>
</head>
<body>
  <section class="card card-front" aria-label="Card front">
    <h1 class="invite-headline">
      <span class="word-large">You</span>
      <span class="word-small">are</span>
      <span class="word-large">Invited</span>
    </h1>
  </section>

  <section class="card card-back" aria-label="Card back">
    <div class="brand">
      <span class="brand-mark"></span>
      <span class="brand-name">GRACE HARBOR MINISTRIES</span>
    </div>
    <p class="contact">
      2480, Cedar Lane - Oakridge, Tx 75210<br>
      1-800-555-0142
    </p>
    <ul class="schedule">
      <li><span>Sunday</span><span class="leader"></span><span>9:00 Am</span></li>
      <li><span>Sunday</span><span class="leader"></span><span>11:00 Am</span></li>
      <li><span>Wed. Bible Class</span><span class="leader"></span><span>7:00 Pm</span></li>
    </ul>
  </section>
</body>
</html>
```